Veltrane Group Business Card Design

The CEO is looking for a new trendy look for his business card.
You can stay with current branding or come up with something new/creative. It can be 3D, including Medical Office buildings. You can use our logo in a variety of colors. Please include name, title, company name, company website, email address, cell number

Target Market(s)

Real Estate Development and Construction

Industry/Entity Type

Health care real estate

Contact Information for Business Card

Rohesh Kamdar, CEO M-604.781.2249 E-roheshkamdar@veltrane.com Address:4180 Lindqvist Ave, Tampa, FL 33482 www.veltrane.com

Font styles to use
Other font styles liked:
• Be creative

Requirements
Must have
• Creative, trendy look
Nice to have
• Please go to our website to get a feel- www. veltrane.com
Should not have
• small fonts

```html
<!DOCTYPE html>
<html lang="en">
<head>
<meta charset="utf-8">
<title>Veltrane Group Business Card</title>
<link rel="stylesheet" href="https://fonts.googleapis.com/css2?family=Montserrat:wght@400;700;800&display=swap">
<style>
  :root {
    --backdrop: #8c6c4b;
    --card-front: #ffffff;
    --card-back: #141414;
    --ink: #111111;
    --ink-soft: #1d1d1d;
    --mark-dim: #2c2c2c;
  }
  * { margin: 0; padding: 0; box-sizing: border-box; }
  html, body {
    width: 900px;
    height: 1200px;
    overflow: hidden;
    background: var(--backdrop);
    font-family: "Montserrat", Arial, sans-serif;
    color: var(--ink);
  }
  .canvas {
    position: relative;
    width: 900px;
    height: 1200px;
  }
  .card {
    position: absolute;
    left: 80px;
    width: 742px;
    height: 440px;
    box-shadow: 0 8px 18px rgba(0, 0, 0, 0.45);
  }
  .card-front { top: 131px; background: var(--card-front); }
  .card-back { top: 638px; background: var(--card-back); }

  .holder {
    position: absolute;
    left: 35px;
    top: 50px;
  }
  .holder-name {
    font-size: 26px;
    font-weight: 700;
    letter-spacing: 0.2px;
    line-height: 1.1;
  }
  .holder-title {
    font-size: 16px;
    font-weight: 400;
    margin-top: 4px;
  }

  .company-name {
    position: absolute;
    right: 24px;
    top: 52px;
    font-size: 40px;
    font-weight: 800;
    letter-spacing: -1px;
    color: var(--ink);
  }

  .contact-list {
    position: absolute;
    left: 36px;
    top: 323px;
    list-style: none;
  }
  .contact-item {
    display: flex;
    align-items: center;
    height: 28px;
    font-size: 16px;
    color: var(--ink-soft);
  }
  .contact-icon {
    width: 16px;
    height: 16px;
    margin-right: 11px;
    fill: var(--ink);
  }

  .address {
    position: absolute;
    left: 541px;
    top: 360px;
    font-size: 16px;
    line-height: 21px;
    font-style: normal;
    color: var(--ink-soft);
  }

  .back-name {
    position: absolute;
    left: 0;
    right: 0;
    top: 195px;
    text-align: center;
    font-size: 66px;
    font-weight: 800;
    letter-spacing: -2px;
    color: var(--mark-dim);
  }
</style>
</head>
<body>
<main class="canvas">
  <section class="card card-front" aria-label="Business card front">
    <div class="holder">
      <div class="holder-name">Rohesh Kamdar</div>
      <div class="holder-title">CEO</div>
    </div>

    <div class="company-name">Veltrane Group</div>

    <ul class="contact-list">
      <li class="contact-item">
        <svg class="contact-icon" viewBox="0 0 24 24" aria-hidden="true">
          <path d="M6.6 10.8c1.4 2.8 3.8 5.1 6.6 6.6l2.2-2.2c.3-.3.7-.4 1-.2 1.1.4 2.3.6 3.6.6.6 0 1 .4 1 1V20c0 .6-.4 1-1 1C10.6 21 3 13.4 3 4c0-.6.4-1 1-1h3.5c.6 0 1 .4 1 1 0 1.3.2 2.5.6 3.6.1.3 0 .7-.2 1L6.6 10.8z"/>
        </svg>
        604.781.2249
      </li>
      <li class="contact-item">
        <svg class="contact-icon" viewBox="0 0 24 24" aria-hidden="true">
          <path d="M3 6h18v1.2l-9 5.6-9-5.6V6zm0 3.4l9 5.6 9-5.6V18H3V9.4z"/>
        </svg>
        roheshkamdar@veltrane.com
      </li>
      <li class="contact-item">
        <svg class="contact-icon" viewBox="0 0 24 24" aria-hidden="true">
          <circle cx="12" cy="12" r="9"/>
          <path d="M12 3v18M3 12h18M12 3c3 3 3 15 0 18M12 3c-3 3-3 15 0 18" stroke="#fff" stroke-width="1.2" fill="none"/>
        </svg>
        www.veltrane.com
      </li>
    </ul>

    <address class="address">4180 Lindqvist Ave,<br>Tampa, FL 33482</address>
  </section>

  <section class="card card-back" aria-label="Business card back">
    <div class="back-name">Veltrane Group</div>
  </section>
</main>
</body>
</html>
```